Website Redesign for Accommodation Directory

We need a redesign for staylistfinderhub.example
The new design needs to include a banner with overlaid text and a 'get started now' button. The overlaid text could be 'Find Hotels in Auckland, New Zealand' for example.
The new design needs to include:
- primary navigation in header
- an accommodation search (left or right column)
- a secondary navigation menu (under the search).
We will need the following font styles (including links for each) defined also please:
h1, h2, h3, h4, h5, h6, p, ul, ol, address, pre
Industry/Entity Type
Accommodation
Look and feel

```html
<!DOCTYPE html>
<html lang="en">
<head>
<meta charset="utf-8">
<title>StayList Finder Hub – Find Accommodation</title>
<link rel="stylesheet" href="https://fonts.googleapis.com/css2?family=Arimo:wght@400;700&family=PT+Sans:wght@400;700&family=Oswald:wght@500&display=swap">
<style>
:root{
  --paper:#f1ebd9;
  --paper-dark:#e6dec6;
  --white:#ffffff;
  --navy:#0c3d72;
  --navy-dark:#062b55;
  --red:#d8101c;
  --orange-link:#e39a32;
  --band:#1f6489;
  --band-dark:#154c6b;
  --text-grey:#7a7a7a;
  --link-blue:#1f5fa8;
  --cat-blue:#1a4f8f;
  --olive:#a8b817;
  --green:#7f9b12;
  --cta-blue:#235f84;
}
*{box-sizing:border-box;margin:0;padding:0}
html,body{width:1200px;height:984px;overflow:hidden}
body{
  position:relative;
  background:radial-gradient(ellipse at 50% 40%,#f6f1e2 0%,var(--paper) 60%,var(--paper-dark) 100%);
  font-family:"Arimo",Arial,sans-serif;
  color:var(--text-grey);
}
a{text-decoration:none;color:inherit}

/* Typography set */
h1{font:700 28px/1.2 "PT Sans",sans-serif;color:var(--white)}
h2{font:700 17px/1.2 "PT Sans",sans-serif;color:var(--navy)}
h3{font:700 16px/1.2 "PT Sans",sans-serif;color:var(--navy)}
h4{font:700 14px/1.2 "PT Sans",sans-serif;color:var(--navy)}
h5{font:700 12px/1.2 "Arimo",sans-serif;color:var(--navy)}
h6{font:700 11px/1.2 "Arimo",sans-serif;color:var(--navy)}
p{font-size:11.5px;line-height:17px}
ul,ol{font-size:11.5px;line-height:17px}
address{font-style:normal;font-size:10px}
pre{font-size:11px}
p a{color:var(--link-blue);font-weight:700}
p a:hover{text-decoration:underline}

/* Header */
.brand{position:absolute;left:142px;top:17px;display:flex;align-items:center;gap:8px}
.brand-mark{width:46px;height:46px;background:var(--red);border-radius:4px}
.brand-name{font:400 36px/1 "Arimo",sans-serif;color:#555;letter-spacing:-1px}
.utility{position:absolute;right:104px;top:16px;font-size:12px;color:var(--orange-link)}
.utility a{color:var(--orange-link)}
.utility span{color:#b9a98a;margin:0 4px}

.main-nav{position:absolute;top:77px;left:0;height:34px}
.main-nav a{
  position:absolute;top:0;height:34px;
  color:var(--white);font:400 13.5px/36px "Arimo",sans-serif;text-align:center;
  background:linear-gradient(#0f4c8a,var(--navy-dark));
  clip-path:polygon(18px 0,100% 0,100% 100%,0 100%);
  border-radius:0 6px 0 0;padding-left:14px;
}
.main-nav a.is-active{background:linear-gradient(#ee2a26,#c9070f)}

/* Page */
.page{position:absolute;left:150px;top:111px;width:900px;height:826px;background:var(--white);box-shadow:0 0 4px rgba(0,0,0,.12)}

.hero{
  position:absolute;left:142px;top:122px;width:916px;height:352px;
  background:linear-gradient(180deg,#8fb6d6 0%,#a9c7df 30%,#7f8f9c 55%,#6d6c68 78%,#4f5b66 100%);
  border:2px solid #9ab9d4;
}
.hero-title{position:absolute;left:352px;top:158px;text-transform:uppercase;text-shadow:0 1px 3px rgba(0,0,0,.5);line-height:32px;font-size:28px}
.hero-cta{
  position:absolute;left:336px;top:401px;width:251px;height:49px;border-radius:25px;
  background:var(--white);box-shadow:0 2px 4px rgba(0,0,0,.35);padding:4px;
}
.hero-cta span{
  display:flex;align-items:center;justify-content:space-between;height:41px;border-radius:21px;
  background:linear-gradient(#ffa23a,#f2620c 55%,#e24a04);padding:0 6px 0 27px;
  font:500 23px/1 "Oswald",sans-serif;color:var(--white);letter-spacing:.2px;
}
.hero-cta svg{display:block}

.intro-band{
  position:absolute;left:150px;top:476px;width:900px;height:85px;
  background:linear-gradient(var(--band),var(--band-dark));
  color:var(--white);font:400 16.5px/19px "PT Sans",sans-serif;padding:16px 330px 0 19px;
}
.fold{position:absolute;top:474px;width:10px;height:10px;background:#0a2c40}
.fold.left{left:140px;clip-path:polygon(0 0,100% 0,100% 100%)}
.fold.right{left:1050px;clip-path:polygon(0 0,100% 0,0 100%)}

.content{position:absolute;left:176px;top:580px;width:560px}
.content p{margin-bottom:17px}

/* Search panel */
.search-panel{
  position:absolute;left:762px;top:281px;width:274px;height:567px;
  background:#e9e9e9;border:1px solid #d0d0d0;border-radius:5px;box-shadow:0 1px 4px rgba(0,0,0,.2);
}
.search-inner{
  position:absolute;left:8px;top:8px;width:257px;height:552px;border:1px solid #cfcfcf;border-radius:4px;
  background:linear-gradient(#ffffff 0,#f4f4f4 20%,#dcdcdc 34%,#ffffff 34.2%,#ffffff 100%);
}
.search-title{position:absolute;left:22px;top:23px;text-transform:uppercase;letter-spacing:.2px}
.search-title em{font-style:normal;color:var(--olive)}
.select{
  position:absolute;left:17px;width:223px;height:35px;border:1px solid #c9c9c9;border-radius:4px;
  background:linear-gradient(#fdfdfd,#ececec);font:400 12px/33px "PT Sans",sans-serif;color:#444;padding-left:12px;
}
.select::after{content:"";position:absolute;right:0;top:0;width:40px;height:33px;border-left:1px solid #cfcfcf}
.select svg{position:absolute;right:14px;top:14px}
.btn-search{
  position:absolute;left:18px;top:137px;width:74px;height:32px;border-radius:3px;
  background:linear-gradient(#9cb829,var(--green) 60%,#6b8509);border:1px solid #5f760b;
  color:var(--white);font:400 16px/30px "PT Sans",sans-serif;text-align:center;
}
.cat-title{position:absolute;left:13px;top:206px;text-transform:uppercase}
.cat-list{position:absolute;left:13px;top:229px;width:245px;list-style:none}
.cat-list li{height:26.25px;border-top:1px dotted #c4c4c4;position:relative}
.cat-list a{display:block;padding-left:13px;color:var(--cat-blue);font-size:11.5px;line-height:26px}
.cat-list a::before{content:"";position:absolute;left:2px;top:9px;border-left:4px solid #9a9a9a;border-top:4px solid transparent;border-bottom:4px solid transparent}

/* Call to action */
.cta-box{
  position:absolute;left:172px;top:865px;width:861px;height:57px;border:1px solid #d3d3d3;border-radius:4px;
  background:linear-gradient(#fdfdfd,#e6e6e6);
  font:400 25px/55px "Arimo",sans-serif;color:var(--cta-blue);text-align:center;
}
.cta-box strong{color:var(--red)}

/* Footer */
.site-footer{position:absolute;left:153px;top:947px;color:#333;line-height:14px;font-size:10px}
.social{position:absolute;left:1015px;top:950px;display:flex;gap:6px}
.social span{width:15px;height:15px;border-radius:2px;display:block}
.social .s1{background:#3b5b98}
.social .s2{background:#3fa9d8}
</style>
</head>
<body>

<header>
  <a class="brand" href="#"><span class="brand-mark"></span><span class="brand-name">staylistfinderhub</span></a>
  <nav class="utility"><a href="#">Free Insurance Quotes</a><span>|</span><a href="#">Free Website Statistics</a><span>|</span><a href="#">Company Reviews</a></nav>
  <nav class="main-nav">
    <a class="is-active" href="#" style="left:483px;width:91px">HOME</a>
    <a href="#" style="left:579px;width:185px">ADD YOUR PROPERTY</a>
    <a href="#" style="left:769px;width:151px">SUPPLIER LOGIN</a>
    <a href="#" style="left:923px;width:127px">CONTACT US</a>
  </nav>
</header>

<div class="page"></div>

<section class="hero" role="img" aria-label="Photo of the Auckland city skyline and harbour waterfront"></section>
<h1 class="hero-title">Find Hotels in Auckland,<br>New Zealand</h1>
<a class="hero-cta" href="#"><span>GET STARTED NOW
  <svg width="34" height="34" viewBox="0 0 34 34"><circle cx="17" cy="17" r="15" fill="#c94a05" stroke="#ffb266" stroke-width="1.5"/><path d="M12 9 L25 17 L12 25 Z" fill="#fff"/></svg></span></a>

<span class="fold left"></span><span class="fold right"></span>
<div class="intro-band">You’ve come to the right place to find Accommodation in Any Country whether it’s a hotel, motel, backpackers, bed and breakfast or beach house you're after you'll find just what you need to enjoy your stay in Any Country.</div>

<main class="content">
  <p>With much to choose from you'll want to find a place that meets your needs. <a href="#">Our accommodation search tool</a> will help you find the perfect place, regardless of what your price, location or style requirements might be.</p>
  <p>Our <a href="#">Any Country accommodation directory</a> is perfect for times when you’ve scored cheap flights, desper-ately need last-minute accommodation or are just planning your next holiday or business trip to Any Country.</p>
  <p>With a great selection of Accommodation options in Any Country from cheap nights staying in budget accom-modation to 5-star luxury Any Country hotels, so you can really treat yourself, you’ll find it all here.</p>
  <p>Using this <a href="#">Any Country Accommodation search tool</a> you'll quickly find a great place to stay offered by providers you can trust and depend on to make sure you get a good night's sleep. From well-known hotel chains to popular beach houses with rave reviews, it's easy to locate welcoming hospitality in Any Country.</p>
  <p>Avoid the hassle of running around Any Country, desperately hoping you'll find a vacancy and a place you won’t regret staying at – just switch on to staylistfinderhub.example to search, click and stay.</p>
</main>

<aside class="search-panel">
  <div class="search-inner">
    <h2 class="search-title">Accommodation <em>Search</em></h2>
    <div class="select" style="top:48px">All Countries<svg width="12" height="7" viewBox="0 0 12 7"><path d="M0 0H12L6 7Z" fill="#1b3f6e"/></svg></div>
    <div class="select" style="top:94px">All Categories<svg width="12" height="7" viewBox="0 0 12 7"><path d="M0 0H12L6 7Z" fill="#1b3f6e"/></svg></div>
    <a class="btn-search" href="#">Search</a>
    <h2 class="cat-title">Categories</h2>
    <ul class="cat-list">
      <li><a href="#">Apartments</a></li>
      <li><a href="#">Backpackers</a></li>
      <li><a href="#">Batch</a></li>
      <li><a href="#">Beach House</a></li>
      <li><a href="#">Bed And Breakfasts</a></li>
      <li><a href="#">Camping Sites</a></li>
      <li><a href="#">Caravan Park</a></li>
      <li><a href="#">Holiday Homes</a></li>
      <li><a href="#">Hostels</a></li>
      <li><a href="#">Hotels</a></li>
      <li><a href="#">Lodges</a></li>
      <li><a href="#">Motels</a></li>
    </ul>
  </div>
</aside>

<a class="cta-box" href="#">Ready to <strong>GET STARTED</strong>? Find Accommodation in Any Country <strong>online now</strong>.</a>

<footer class="site-footer">
  <address>© 2011 StayList Finder Hub<br>Find Accommodation in Any Country - Accommodation Any Country | Recommend us | Contact Us | Sitemap</address>
</footer>
<div class="social"><span class="s1"></span><span class="s2"></span></div>

</body>
</html>
```